Beacon Advisory Website

I currently have a website www.beaconadvisoryinc.com. We are a IT Consulting Company. Our website will pretty much tell out our services. I am looking to enhance my website and make it look more professional. Looking for very classy and Contemporary look and design for my website.

It Company

```html
<!DOCTYPE html>
<html lang="en">
<head>
<meta charset="utf-8">
<title>Beacon Advisory</title>
<link href="https://fonts.googleapis.com/css2?family=Montserrat:wght@300;400;600;700&family=Open+Sans:wght@400;600&display=swap" rel="stylesheet">
<style>
:root{
  --blue:#1f8ad8;
  --blue-dark:#13609f;
  --blue-soft:#3a9fe6;
  --navy:#15212d;
  --navy-2:#1d2c3b;
  --ink:#2b3a48;
  --white:#ffffff;
  --mist:#c9d6e2;
  --band:#5c7a97;
}
*{box-sizing:border-box;margin:0;padding:0}
html,body{width:1200px;height:4060px;overflow:hidden}
body{font-family:"Open Sans",Arial,sans-serif;color:var(--white);background:var(--navy);position:relative}
section,header,footer{position:absolute;left:0;width:1200px;overflow:hidden}
.photo{position:absolute;inset:0}
h1,h2,h3,.brand,.nav a,.btn{font-family:"Montserrat",Arial,sans-serif}
.btn{display:inline-block;font-size:15px;font-weight:600;text-transform:uppercase;letter-spacing:.5px;padding:12px 24px}
.eyebrow{font-family:"Montserrat",Arial,sans-serif;color:var(--blue-soft);font-size:20px;text-transform:uppercase;letter-spacing:1px;text-align:center}
.section-title{font-family:"Montserrat",Arial,sans-serif;font-weight:300;font-size:40px;text-align:center;text-transform:none}
.section-title b{font-weight:600;text-transform:uppercase}

/* hero */
.hero{top:0;height:660px}
.hero .photo{background:linear-gradient(100deg,#1a2531 0%,#34414f 45%,#56606b 70%,#2b3743 100%)}
.site-nav{position:absolute;top:0;left:0;width:1200px;height:80px;background:rgba(13,22,32,.55);display:flex;align-items:center;padding:0 90px}
.brand{display:flex;align-items:center;gap:12px;font-size:24px;font-weight:700;color:var(--white)}
.brand-mark{width:34px;height:34px;background:var(--blue)}
.nav{margin-left:auto;display:flex;gap:4px}
.nav a{color:var(--white);text-decoration:none;font-size:14px;text-transform:uppercase;padding:10px 14px}
.nav a.active{color:var(--blue-soft)}
.hero-copy{position:absolute;left:75px;top:190px;width:480px}
.hero-copy .we{font-family:"Montserrat",sans-serif;font-size:30px;font-weight:600}
.hero-copy h1{font-size:54px;font-weight:700;line-height:1.1;margin-bottom:14px}
.hero-copy p{font-size:22px;line-height:1.4;margin-bottom:26px}
.btn-light{background:var(--white);color:var(--blue-dark);font-size:13px;padding:12px 20px}

/* newsletter */
.newsletter{top:660px;height:240px;background:linear-gradient(90deg,var(--blue-dark),var(--blue) 60%,var(--blue-dark))}
.newsletter h2{position:absolute;left:75px;top:70px;font-size:32px;font-weight:600;line-height:1.25;text-transform:uppercase}
.subscribe{position:absolute;left:665px;top:72px;display:flex}
.subscribe .field{width:350px;height:42px;background:var(--white);color:#8a97a4;font-size:14px;padding:11px 16px}
.subscribe .btn{background:var(--blue-soft);color:var(--white);padding:11px 24px;font-size:14px;text-transform:none;border:1px solid rgba(255,255,255,.6)}
.newsletter .note{position:absolute;left:780px;top:132px;font-size:15px;font-weight:600}

/* services */
.services{top:900px;height:620px}
.services .photo{background:linear-gradient(180deg,#2a3b4c,#1c2a38 55%,#233444)}
.services .eyebrow{position:absolute;top:40px;width:100%}
.services .section-title{position:absolute;top:66px;width:100%}
.tab-list{position:absolute;left:128px;top:135px;width:340px;border:1px solid rgba(58,159,230,.7);background:rgba(16,40,64,.55);list-style:none}
.tab-list li{display:flex;align-items:center;gap:16px;height:62px;padding:0 20px;font-family:"Montserrat",sans-serif;font-size:15px;text-transform:uppercase;border-bottom:1px solid rgba(58,159,230,.35)}
.tab-list li:last-child{border-bottom:none}
.tab-list li.active{background:var(--blue)}
.tab-list svg{width:22px;height:22px;flex:none}
.tab-panel{position:absolute;left:468px;top:135px;width:604px;height:373px;background:rgba(19,40,60,.78);border:1px solid rgba(58,159,230,.7);padding:22px 30px}
.tab-panel h3{color:var(--blue-soft);font-size:28px;font-weight:600;text-transform:uppercase;margin-bottom:10px}
.tab-panel p{font-size:15px;line-height:1.55;color:#d7e2ec}
.features{display:flex;gap:60px;margin-top:34px;justify-content:center}
.feature{display:flex;align-items:center;gap:10px;font-size:14px}
.feature svg{width:30px;height:30px}

/* cta */
.cta{top:1520px;height:210px;background:linear-gradient(90deg,#e8f1f8,#c9def0 60%,#dbe9f5)}
.cta h2{position:absolute;left:75px;top:62px;width:760px;font-size:32px;font-weight:600;line-height:1.25;text-transform:uppercase;color:var(--blue-dark)}
.cta h2 .hl{color:var(--blue)}
.cta .btn{position:absolute;left:895px;top:84px;background:var(--blue);color:var(--white);text-transform:none;font-size:16px}

/* gallery */
.gallery{top:1730px;height:630px}
.gallery .photo{background:linear-gradient(180deg,#1b2733,#24303c)}
.gallery .eyebrow{position:absolute;top:45px;width:100%}
.gallery .section-title{position:absolute;top:70px;width:100%}
.filters{position:absolute;top:130px;left:0;width:100%;display:flex;justify-content:center;gap:40px;font-size:14px;color:#c5d1dc}
.filters .active{color:var(--white);border-bottom:2px solid var(--blue-soft);padding-bottom:4px}
.grid{position:absolute;left:80px;top:170px;width:1040px;display:grid;grid-template-columns:repeat(4,1fr);gap:8px}
.tile{height:114px;background:linear-gradient(135deg,#8d9aa6,#d6dde3 50%,#6f7e8c)}
.tile:nth-child(3n+2){background:linear-gradient(135deg,#c8cfd6,#6a7987 55%,#aeb8c1)}
.tile.feature-tile{background:rgba(31,138,216,.85);display:flex;flex-direction:column;align-items:center;justify-content:center;gap:10px;font-family:"Montserrat",sans-serif;font-size:18px;text-transform:uppercase}
.gallery .btn{position:absolute;left:530px;top:562px;background:var(--blue);color:var(--white);font-size:14px}

/* stats */
.stats{top:2360px;height:230px;background:linear-gradient(90deg,var(--blue-dark),var(--blue) 50%,var(--blue-dark));display:flex;justify-content:space-around;padding:0 80px;align-items:center}
.stat{text-align:center;width:200px}
.stat svg{width:44px;height:44px;margin-bottom:10px}
.stat strong{display:block;font-family:"Montserrat",sans-serif;font-size:36px;font-weight:400}
.stat span{font-size:13px;text-transform:uppercase;letter-spacing:.5px}

/* testimonials */
.testimonials{top:2590px;height:660px}
.testimonials .photo{background:linear-gradient(180deg,#4b5866,#6e7985 50%,#3a4653)}
.testimonials .shade{position:absolute;inset:0;background:rgba(20,32,44,.45)}
.testimonials .eyebrow{position:absolute;top:50px;width:100%}
.testimonials .section-title{position:absolute;top:74px;width:100%}
.quote-mark{position:absolute;left:570px;top:150px;font-family:Georgia,serif;font-size:110px;line-height:1;color:var(--white)}
.quote{position:absolute;left:210px;top:260px;width:780px;text-align:center;font-size:15px;line-height:1.6;color:#eef3f7}
.author{position:absolute;top:380px;width:100%;text-align:center}
.author strong{display:block;font-family:"Montserrat",sans-serif;font-size:18px;font-weight:600}
.author span{font-size:13px;color:#d2dce5}
.avatar{position:absolute;left:555px;top:440px;width:90px;height:90px;border:3px solid var(--white);background:linear-gradient(160deg,#d9c7b5,#8a7766)}

/* partners */
.partners{top:3250px;height:150px;background:linear-gradient(180deg,#6d89a4,var(--band));display:flex;align-items:center;justify-content:space-around;padding:0 60px}
.partner{width:120px;height:40px;border-radius:20px;background:rgba(255,255,255,.45)}

/* contact */
.contact{top:3400px;height:600px}
.contact .photo{background:linear-gradient(180deg,#2a3440,#4a4236 45%,#5a4a3a 70%,#2c2a28)}
.contact .brand-line{position:absolute;top:45px;width:100%;text-align:center;font-family:"Montserrat",sans-serif;font-size:20px;color:var(--blue-soft)}
.contact .section-title{position:absolute;top:72px;width:100%}
.form{position:absolute;left:200px;top:150px;width:340px}
.form h3{font-size:26px;font-weight:400;text-transform:uppercase;text-align:center;margin-bottom:16px}
.input{background:var(--white);color:#8a97a4;font-size:13px;height:36px;padding:9px 12px;margin-bottom:10px}
.input.area{height:110px}
.form .btn{display:block;width:100%;text-align:center;background:var(--blue);color:var(--white);font-size:15px}
.info{position:absolute;left:730px;top:195px;width:380px}
.info h3{color:var(--blue-soft);font-size:24px;font-weight:600;text-transform:uppercase;margin-bottom:28px}
.info-row{display:flex;gap:22px;align-items:flex-start;margin-bottom:34px;font-size:15px;line-height:1.5}
.info-row svg{width:26px;height:26px;flex:none;margin-top:2px}

/* footer */
.site-footer{top:4000px;height:60px;background:var(--navy);display:flex;align-items:center;padding:0 80px;font-size:13px;color:#9fb0c0}
.site-footer .copy{margin-left:360px}
.social{margin-left:auto;display:flex;gap:14px}
.social i{width:16px;height:16px;background:#7f93a6;display:block}
</style>
</head>
<body>

<header class="hero">
  <div class="photo" role="img" aria-label="Businessman in a suit standing in front of a team meeting in an office"></div>
  <nav class="site-nav">
    <div class="brand"><span class="brand-mark"></span>Beacon Advisory</div>
    <div class="nav">
      <a class="active" href="#">Home</a><a href="#">Company</a><a href="#">Services</a><a href="#">Solutions</a><a href="#">Resources</a><a href="#">Career</a><a href="#">Contact Us</a>
    </div>
  </nav>
  <div class="hero-copy">
    <div class="we">WE ARE</div>
    <h1>BEACON Advisory</h1>
    <p>Lorem Ipsum is simply dummy text of the printing and typesetting industry.</p>
    <span class="btn btn-light">Appoint Now</span>
  </div>
</header>

<section class="newsletter">
  <h2>Subscribe to get<br>newsletter</h2>
  <div class="subscribe"><div class="field">Enter mail here</div><span class="btn">Subscribe</span></div>
  <div class="note">Subscribe Now to Get in Touch with us</div>
</section>

<section class="services">
  <div class="photo" role="img" aria-label="Colleagues working together at laptops"></div>
  <div class="eyebrow">Services</div>
  <h2 class="section-title">We <b>Provide</b></h2>
  <ul class="tab-list">
    <li class="active"><svg viewBox="0 0 24 24" fill="none" stroke="#fff" stroke-width="2"><rect x="3" y="4" width="18" height="12"/><path d="M8 20h8M12 16v4"/></svg>Technology</li>
    <li><svg viewBox="0 0 24 24" fill="none" stroke="#fff" stroke-width="2"><rect x="3" y="7" width="18" height="13"/><path d="M9 7V4h6v3"/></svg>Business</li>
    <li><svg viewBox="0 0 24 24" fill="none" stroke="#fff" stroke-width="2"><rect x="4" y="4" width="7" height="7"/><rect x="13" y="4" width="7" height="7"/><rect x="4" y="13" width="7" height="7"/><rect x="13" y="13" width="7" height="7"/></svg>Application</li>
    <li><svg viewBox="0 0 24 24" fill="none" stroke="#fff" stroke-width="2"><path d="M8 7l-5 5 5 5M16 7l5 5-5 5"/></svg>Development</li>
    <li><svg viewBox="0 0 24 24" fill="none" stroke="#fff" stroke-width="2"><path d="M4 20L20 4M4 4l16 16"/></svg>Enterprise Integration</li>
    <li><svg viewBox="0 0 24 24" fill="none" stroke="#fff" stroke-width="2"><circle cx="12" cy="8" r="4"/><path d="M4 21c0-4 4-6 8-6s8 2 8 6"/></svg>IT Consulting</li>
  </ul>
  <div class="tab-panel">
    <h3>Technology</h3>
    <p>Lorem Ipsum is simply dummy text of the printing and typesetting industry. Lorem Ipsum has been the industry's standard dummy text ever since the 1500s, when an unknown printer took a galley of type and scrambled it to make a type specimen book. It has survived not only five centuries, but also the leap into electronic typesetting, remaining essentially unchanged. It was popularised in the 1960s with the release of Letraset sheets containing Lorem Ipsum passages, and more recently with desktop publishing software like Aldus PageMaker including versions of Lorem Ipsum.</p>
    <div class="features">
      <div class="feature"><svg viewBox="0 0 30 30" fill="none" stroke="#fff" stroke-width="2"><circle cx="15" cy="15" r="12"/><path d="M10 15l4 4 7-8"/></svg>Training</div>
      <div class="feature"><svg viewBox="0 0 30 30" fill="none" stroke="#fff" stroke-width="2"><circle cx="15" cy="15" r="12"/><path d="M9 15a6 6 0 0 1 11-3M21 15a6 6 0 0 1-11 3"/></svg>Technology Refresh</div>
      <div class="feature"><svg viewBox="0 0 30 30" fill="none" stroke="#fff" stroke-width="2"><circle cx="15" cy="15" r="12"/><path d="M9 20V14M15 20V10M21 20v-8"/></svg>Capacity</div>
    </div>
  </div>
</section>

<section class="cta">
  <h2><span class="hl">The fastest way</span> to grow your business with the leader in technology</h2>
  <span class="btn">Make an Appointment</span>
</section>

<section class="gallery">
  <div class="photo" role="img" aria-label="Dark desk with laptop and coffee"></div>
  <div class="eyebrow">Gallery</div>
  <h2 class="section-title">See <b>Our Work</b></h2>
  <div class="filters"><span class="active">All</span><span>Dashboards</span><span>Data warehousing</span><span>BPM</span></div>
  <div class="grid">
    <div class="tile" role="img" aria-label="Team portrait in an office"></div>
    <div class="tile" role="img" aria-label="Meeting around a conference table"></div>
    <div class="tile feature-tile">Project Name
      <svg width="60" height="26" viewBox="0 0 60 26" fill="none" stroke="#fff" stroke-width="2"><circle cx="15" cy="13" r="11"/><path d="M11 13h8M15 9v8"/><circle cx="45" cy="13" r="11"/><path d="M41 9l8 8M49 9l-8 8"/></svg>
    </div>
    <div class="tile" role="img" aria-label="Person working at a laptop"></div>
    <div class="tile" role="img" aria-label="Colleagues discussing documents"></div>
    <div class="tile" role="img" aria-label="Presentation in a meeting room"></div>
    <div class="tile" role="img" aria-label="Handshake in an office"></div>
    <div class="tile" role="img" aria-label="Group reviewing a screen"></div>
    <div class="tile" role="img" aria-label="Business team standing together"></div>
    <div class="tile" role="img" aria-label="Workshop around a table"></div>
    <div class="tile" role="img" aria-label="Two people in conversation"></div>
    <div class="tile" role="img" aria-label="Consultant presenting to clients"></div>
  </div>
  <span class="btn">Load More</span>
</section>

<section class="stats">
  <div class="stat"><svg viewBox="0 0 44 44" fill="none" stroke="#fff" stroke-width="2"><rect x="6" y="14" width="32" height="22"/><path d="M16 14V8h12v6"/></svg><strong>2,500</strong><span>Project Completed</span></div>
  <div class="stat"><svg viewBox="0 0 44 44" fill="none" stroke="#fff" stroke-width="2"><path d="M6 24l10-10 8 6 14-10"/><path d="M12 30l6 6 6-4 8 4"/></svg><strong>400</strong><span>Happy Clients</span></div>
  <div class="stat"><svg viewBox="0 0 44 44" fill="none" stroke="#fff" stroke-width="2"><circle cx="14" cy="15" r="5"/><circle cx="30" cy="15" r="5"/><path d="M4 34c0-6 5-9 10-9s10 3 10 9M20 34c0-6 5-9 10-9s10 3 10 9"/></svg><strong>100</strong><span>Team Members</span></div>
  <div class="stat"><svg viewBox="0 0 44 44" fill="none" stroke="#fff" stroke-width="2"><circle cx="22" cy="17" r="10"/><path d="M16 26l-4 12 10-5 10 5-4-12"/></svg><strong>20</strong><span>Awards Won</span></div>
</section>

<section class="testimonials">
  <div class="photo" role="img" aria-label="Business people meeting around a table"></div>
  <div class="shade"></div>
  <div class="eyebrow">Testimonials</div>
  <h2 class="section-title">What <b>Clients</b> Say</h2>
  <div class="quote-mark">&ldquo;</div>
  <p class="quote">"Lorem Ipsum is simply dummy text of the printing and typesetting industry. Lorem Ipsum has been the industry's standard dummy text ever since the 1500s, when an unknown printer took a galley of type and scrambled it to make a type specimen book. It has survived not only five centuries, but also the leap into electronic typesetting, remaining essentially unchanged. It was popularised in the 1960s with the release of Letraset sheets containing Lorem Ipsum passages."</p>
  <div class="author"><strong>Nora Whitfield</strong><span>General Manager</span></div>
  <div class="avatar" role="img" aria-label="Client portrait"></div>
</section>

<section class="partners" aria-label="Partners">
  <div class="partner"></div><div class="partner"></div><div class="partner"></div><div class="partner"></div><div class="partner"></div><div class="partner"></div>
</section>

<section class="contact">
  <div class="photo" role="img" aria-label="Desert road leading toward mountains"></div>
  <div class="brand-line">Beacon Advisory</div>
  <h2 class="section-title"><b>Contact</b> Us</h2>
  <div class="form">
    <h3>Send a Message</h3>
    <div class="input">Name</div>
    <div class="input">E-mail</div>
    <div class="input">Subject</div>
    <div class="input area">Message</div>
    <span class="btn">Submit</span>
  </div>
  <div class="info">
    <h3>Contact Information</h3>
    <div class="info-row"><svg viewBox="0 0 26 26" fill="none" stroke="#fff" stroke-width="2"><path d="M6 3h5l2 6-3 2a12 12 0 0 0 5 5l2-3 6 2v5c0 1-1 2-2 2A19 19 0 0 1 4 5c0-1 1-2 2-2z"/></svg><div>North America: (800) 555-0142<br>France: +33 1 55 50 01 42</div></div>
    <div class="info-row"><svg viewBox="0 0 26 26" fill="none" stroke="#fff" stroke-width="2"><rect x="3" y="6" width="20" height="14"/><path d="M3 6l10 8 10-8"/></svg><div>hello@beaconadvisoryinc.com</div></div>
    <div class="info-row"><svg viewBox="0 0 26 26" fill="none" stroke="#fff" stroke-width="2"><path d="M13 24s-8-8-8-14a8 8 0 0 1 16 0c0 6-8 14-8 14z"/><circle cx="13" cy="10" r="3"/></svg><div>Northway Ltd, 410 Lantern St. 3rd Floor<br>Easton, ON K0A 2B0 Canada</div></div>
  </div>
</section>

<footer class="site-footer">
  <span class="copy">© Beacon Advisory 20xx. All Rights Reserved</span>
  <div class="social"><i></i><i></i><i></i><i></i></div>
</footer>

</body>
</html>
```